Human Resource Consulting practice needs a business card design

We need a business card design (double sided colour) for our Human Resource (HR) consulting practice in regional New South Wales, australia. Our business name is Staff Compass. We support small and medium business across the Mid North Coast of New South Wales by providing them with outsourced HR support, services and products to help them achieve compliance with workplace legislation and across all areas of the employment lifecycle from recruitment to termination and everything in between. Our corporate colours are hot pink and black. The final design should communicate professionalism, trust, people focus.
I have attached the current (old) business card for your reference.

Target Market(s)

Business owners and high level managers

Industry/Entity Type

Business

Contact Information for Business Card

Name
Title
Phone no
Mobile no
Address
PO Box
email address
website

Colors
e34197

Requirements
Must have
• Tempate for changing business card personal details including Name, position title, mobile number, email address.
• Keep current logo and colours as per attached
• Logo must be presented in 2 colours or black only not white
Nice to have
• One side logo and graphic only other side logo and personal details
Should not have
• Should not be the same as the current version (attached) but a modern interpretation.
• Does not need a busy reverse side with our list of services as per current version. I feel this is too busy.
• No photos

```html
<!DOCTYPE html>
<html lang="en">
<head>
<meta charset="utf-8">
<title>Staff Compass – Business Card</title>
<link rel="stylesheet" href="https://fonts.googleapis.com/css2?family=Jura:wght@500;600;700&display=swap">
<style>
  :root {
    --hot-pink: #e3218f;
    --charcoal: #3a3a3c;
    --ink: #2b2b2d;
    --paper-light: #ffffff;
    --paper-shade: #e4e4e6;
    --backdrop: #c9ccd1;
    --on-dark: #f4f4f4;
  }
  * { box-sizing: border-box; margin: 0; padding: 0; }
  html, body {
    width: 1200px;
    height: 864px;
    overflow: hidden;
  }
  body {
    background: var(--backdrop);
    font-family: "Jura", sans-serif;
    position: relative;
  }
  .card {
    position: absolute;
    top: 277px;
    width: 540px;
    height: 309px;
    overflow: hidden;
    background: radial-gradient(circle at 45% 45%, var(--paper-light) 0%, var(--paper-shade) 100%);
    box-shadow: 0 6px 18px rgba(0, 0, 0, 0.18);
  }
  .card--front { left: 40px; }
  .card--back { left: 620px; }

  .wordmark {
    font-family: "Jura", sans-serif;
    font-weight: 700;
    color: var(--ink);
    letter-spacing: 0.01em;
    white-space: nowrap;
  }
  .card--front .wordmark {
    position: absolute;
    left: 50%;
    top: 50%;
    transform: translate(-50%, -50%);
    font-size: 46px;
  }
  .card--back .wordmark {
    position: absolute;
    left: 34px;
    top: 108px;
    font-size: 26px;
  }

  .wave {
    position: absolute;
    inset: 0;
    width: 100%;
    height: 100%;
  }
  .wave__accent { fill: var(--hot-pink); }
  .wave__base { fill: var(--charcoal); }

  .person {
    position: absolute;
    left: 60px;
    top: 204px;
  }
  .person__name {
    color: var(--hot-pink);
    font-weight: 700;
    font-size: 16px;
    letter-spacing: 0.06em;
    text-transform: uppercase;
  }
  .person__title {
    color: var(--ink);
    font-weight: 600;
    font-size: 12.5px;
    margin-top: 2px;
    padding-left: 28px;
  }

  .contact {
    position: absolute;
    right: 22px;
    top: 40px;
    list-style: none;
    text-align: right;
    color: var(--on-dark);
    font-size: 10.5px;
    font-weight: 600;
    line-height: 1.35;
  }
  .contact__item {
    display: flex;
    justify-content: flex-end;
    align-items: center;
    gap: 6px;
    margin-bottom: 9px;
  }
  .contact__address { margin-bottom: 16px; }
  .contact__icon {
    width: 11px;
    height: 11px;
    flex: none;
    fill: none;
    stroke: var(--on-dark);
    stroke-width: 1.4;
  }
</style>
</head>
<body>

  <section class="card card--front" aria-label="Card front">
    <p class="wordmark">Staff Compass</p>
  </section>

  <section class="card card--back" aria-label="Card back">
    <svg class="wave" viewBox="0 0 540 309" preserveAspectRatio="none" aria-hidden="true">
      <path class="wave__accent" d="M318 0 C 262 62, 300 196, 222 244 C 170 276, 110 288, 60 309 L 540 309 L 540 0 Z"/>
      <path class="wave__base" d="M350 0 C 296 64, 330 206, 252 254 C 206 282, 150 294, 110 309 L 540 309 L 540 0 Z"/>
    </svg>

    <p class="wordmark">Staff Compass</p>

    <div class="person">
      <p class="person__name">Daniel Whitford</p>
      <p class="person__title">Managing Director</p>
    </div>

    <ul class="contact">
      <li class="contact__item contact__address">14 Harbour Street,<br>Port Macquarie NSW</li>
      <li class="contact__item">02 5550 1842
        <svg class="contact__icon" viewBox="0 0 12 12" aria-hidden="true"><path d="M2 1.5 L4 1.5 L5 4 L3.8 5 C4.5 6.6 5.4 7.5 7 8.2 L8 7 L10.5 8 L10.5 10 C6 10.5 1.5 6 2 1.5 Z"/></svg>
      </li>
      <li class="contact__item">0455 501 842
        <svg class="contact__icon" viewBox="0 0 12 12" aria-hidden="true"><rect x="3" y="1" width="6" height="10" rx="1"/><line x1="5" y1="9.2" x2="7" y2="9.2"/></svg>
      </li>
      <li class="contact__item">02 5550 1843
        <svg class="contact__icon" viewBox="0 0 12 12" aria-hidden="true"><rect x="1.5" y="4" width="9" height="6" rx="0.8"/><rect x="3.5" y="1.5" width="5" height="2.5"/></svg>
      </li>
      <li class="contact__item">hello@staffcompass.example
        <svg class="contact__icon" viewBox="0 0 12 12" aria-hidden="true"><rect x="1" y="2.5" width="10" height="7" rx="0.8"/><path d="M1 3 L6 7 L11 3"/></svg>
      </li>
      <li class="contact__item">www.staffcompass.example
        <svg class="contact__icon" viewBox="0 0 12 12" aria-hidden="true"><circle cx="6" cy="6" r="4.8"/><ellipse cx="6" cy="6" rx="2" ry="4.8"/><line x1="1.2" y1="6" x2="10.8" y2="6"/></svg>
      </li>
    </ul>
  </section>

</body>
</html>
```